Business Card for beauty technology startup

Design Glimora Business Card for a Beauty, based on the website identity and colors (https://www.glimora-example.com).
Glimora is a beauty tech startup that gathers helpful product info for beauty lovers and consumers (such as availability on stores, price range and product reviews) for makeup products. The card design must be young, colorful but clean, and very modern.

Target Market(s)

woman, 15-35

Industry/Entity Type

Cosmetics

Contact Information for Business Card

Full Name, address, phone

Font styles to use
Other font styles liked:
• Advent Pro

Colors
e34297
86cfc6
ffffff
5c5c5c
e8e8e8
e667a6
b2b2b2

Requirements
Must have
• One full colored side with a creative design and another with card info
• Use Color palette: #95C5C5 and/or #D38AA5
• Use fonts: Advent Pro
• Use website identity: https://www.glimora-example.com
Nice to have
• If needed extra font: Roboto

```html
<!DOCTYPE html>
<html lang="en">
<head>
<meta charset="utf-8">
<title>Glimora Business Card</title>
<link rel="stylesheet" href="https://fonts.googleapis.com/css2?family=Open+Sans:wght@300;400;700&display=swap">
<style>
  :root {
    --backdrop: #e8e8e8;
    --card-white: #ffffff;
    --mauve: #b5788f;
    --mauve-deep: #a86a82;
    --text-light: #ffffff;
  }
  * { box-sizing: border-box; margin: 0; padding: 0; }
  html, body {
    width: 1200px; height: 900px; overflow: hidden;
    background: var(--backdrop);
    font-family: "Open Sans", Arial, sans-serif;
  }
  .canvas {
    width: 1200px; height: 900px;
    display: flex; flex-direction: column;
    align-items: center; justify-content: center; gap: 60px;
  }
  .card {
    width: 630px; height: 360px;
    position: relative; overflow: hidden;
    box-shadow: 0 6px 18px rgba(0,0,0,0.15);
  }
  /* Front */
  .card-front {
    background: var(--card-white);
    display: flex; flex-direction: column;
    align-items: center; justify-content: center; gap: 26px;
  }
  .brand-dot {
    width: 78px; height: 78px; border-radius: 50%;
    border: 3px solid var(--mauve);
  }
  .brand-name {
    font-weight: 300; font-size: 46px; letter-spacing: 12px;
    color: var(--mauve); padding-left: 12px;
  }
  /* Back */
  .card-back { background: var(--mauve); }
  .back-circle {
    position: absolute; width: 330px; height: 330px; border-radius: 50%;
    background: var(--card-white);
    right: 22px; top: -28px;
  }
  .contact {
    position: absolute; left: 44px; bottom: 34px;
    color: var(--text-light);
  }
  .contact-name { font-weight: 700; font-size: 17px; letter-spacing: 0.3px; }
  .contact-role { font-weight: 400; font-size: 16px; margin-bottom: 18px; }
  .contact-address { font-size: 14px; line-height: 1.35; margin-bottom: 12px; }
  .contact-list { list-style: none; font-size: 14px; line-height: 1.45; }
  .contact-list li { display: flex; align-items: center; gap: 9px; }
  .contact-list svg { width: 13px; height: 13px; fill: var(--text-light); flex: none; }
</style>
</head>
<body>
<main class="canvas">
  <section class="card card-front" aria-label="Card front">
    <div class="brand-dot"></div>
    <div class="brand-name">GLIMORA</div>
  </section>

  <section class="card card-back" aria-label="Card back">
    <div class="back-circle"></div>
    <div class="contact">
      <div class="contact-name">MARA ELLISON</div>
      <div class="contact-role">CEO/FOUNDER</div>
      <div class="contact-address">214 Lilac Court<br>Portland, Oregon 97201</div>
      <ul class="contact-list">
        <li><svg viewBox="0 0 16 16"><path d="M3 1h3l1.5 4-2 1.3a9 9 0 0 0 4.2 4.2L11 8.5l4 1.5v3a2 2 0 0 1-2 2A12 12 0 0 1 1 3a2 2 0 0 1 2-2z"/></svg>555 201 4837</li>
        <li><svg viewBox="0 0 16 16"><path d="M4 0h8a1 1 0 0 1 1 1v14a1 1 0 0 1-1 1H4a1 1 0 0 1-1-1V1a1 1 0 0 1 1-1zm1 2v10h6V2zm3 11a1 1 0 1 0 0 2 1 1 0 0 0 0-2z"/></svg>555 318 7260</li>
        <li><svg viewBox="0 0 16 16"><path d="M4 1h7l2 2v4H4zM1 8h14v7H1zm3 2v1h2v-1zm4 0v1h2v-1z"/></svg>555 742 0915</li>
        <li><svg viewBox="0 0 16 16"><path d="M1 3h14v10H1zm1.5 1.5L8 9l5.5-4.5v-.2H2.5z"/></svg>hello@glimora-example.com</li>
        <li><svg viewBox="0 0 16 16"><path d="M8 0a8 8 0 1 0 0 16A8 8 0 0 0 8 0zm0 2a6 6 0 0 1 5.9 5H10a10 10 0 0 0-1.3-4.9A6 6 0 0 1 8 2zM2.1 9H6a10 10 0 0 0 1.3 4.9A6 6 0 0 1 2.1 9z"/></svg>www.glimora-example.com</li>
      </ul>
    </div>
  </section>
</main>
</body>
</html>
```